TL - business card

Tallow Partners is an insurance brokerage firm, inovative, proactive, vigorous, which aims to become the leader of the insurance brokers in Anfrica. We should like to get some designs which should be avoided also in Gray / Metallic for the Administration and Orange / Blue for the Managers (ike in the picture sent). The Blue / Green logo is not the correct one, but the source of the file. Please adjust the color accordingly for the business cards. 1 / Orange / Blue 2 / Gray / Metallic We want something classic but which is transmitted strenght, inovation, modernity and most of all, rapidity. We want something start-up like, very punchy and catching eye remaining profesional at the same time. Name: Dorian Whitlock Function: Managing Director Address: N ° 17/18 Rua Veloso - R / C 2B Direita - Bairro Mutamba - Luanda Tel: (+244) 947 582 316 Email: dorian.whitlock@tallow-p.example Website: www.tallow-p. example We want classic in the front and creative, colorfull at the back. The cards will be printed in relief, with very high quality of paper.
Insurance Broker
Colors
Designer to choose colors to be used in the design.

```html
<!DOCTYPE html>
<html lang="en">
<head>
<meta charset="utf-8">
<title>Tallow Partners – Business Card</title>
<link rel="stylesheet" href="https://fonts.googleapis.com/css2?family=Montserrat:wght@400;500;600;700&display=swap">
<style>
  :root {
    --backdrop: #2a2a2a;
    --sky: #27aae1;
    --paper: #f3f3f3;
    --ink: #5a5a5a;
    --brand-green: #1e9a48;
    --white: #ffffff;
  }
  html, body {
    margin: 0;
    padding: 0;
    width: 1200px;
    height: 750px;
    overflow: hidden;
    background: var(--backdrop);
    font-family: "Montserrat", Arial, sans-serif;
  }
  .stage {
    position: relative;
    width: 1200px;
    height: 750px;
  }
  .card {
    position: absolute;
    width: 520px;
    height: 297px;
    box-shadow: 0 10px 24px rgba(0,0,0,.55);
    overflow: hidden;
  }
  .card--front {
    left: 53px;
    top: 226px;
    background: var(--sky);
  }
  .card--back {
    left: 627px;
    top: 226px;
    background: var(--paper);
  }
  .front-brand {
    position: absolute;
    left: 0;
    right: 0;
    top: 112px;
    display: flex;
    align-items: center;
    justify-content: center;
    gap: 12px;
  }
  .brand-dot {
    width: 26px;
    height: 26px;
    border-radius: 50%;
    border: 3px solid var(--white);
    box-sizing: border-box;
  }
  .front-brand .brand-name {
    color: var(--white);
    font-weight: 700;
    font-size: 26px;
    letter-spacing: 1px;
    text-transform: uppercase;
  }
  .back-brand {
    position: absolute;
    right: 30px;
    top: 62px;
    display: flex;
    align-items: center;
    gap: 8px;
  }
  .back-brand .brand-dot {
    width: 18px;
    height: 18px;
    border-color: var(--brand-green);
  }
  .back-brand .brand-name {
    color: var(--brand-green);
    font-weight: 700;
    font-size: 18px;
    letter-spacing: .5px;
    text-transform: uppercase;
  }
  .contact {
    position: absolute;
    left: 30px;
    top: 52px;
    color: var(--ink);
  }
  .contact__name {
    margin: 0;
    color: var(--sky);
    font-weight: 600;
    font-size: 22px;
    letter-spacing: .5px;
  }
  .contact__role {
    margin: 2px 0 10px;
    font-size: 12px;
  }
  .contact__address {
    margin: 0 0 10px;
    font-size: 12.5px;
    line-height: 1.45;
  }
  .contact__line {
    display: flex;
    align-items: center;
    gap: 7px;
    font-size: 12.5px;
    line-height: 1.6;
  }
  .contact__line svg {
    width: 10px;
    height: 10px;
    flex: none;
  }
  .rule {
    position: absolute;
    left: 200px;
    right: 30px;
    top: 106px;
    height: 1px;
    background: var(--sky);
  }
</style>
</head>
<body>
<main class="stage">
  <section class="card card--front" aria-label="Card front">
    <div class="front-brand">
      <span class="brand-dot"></span>
      <span class="brand-name">Tallow Partners</span>
    </div>
  </section>

  <section class="card card--back" aria-label="Card back">
    <div class="contact">
      <h1 class="contact__name">Dorian Whitlock</h1>
      <p class="contact__role">Managing Director</p>
      <p class="contact__address">
        N ° 17/18 Rua Veloso<br>
        R / C 2B Direita<br>
        Bairro Mutamba - Luanda
      </p>
      <div class="contact__line">
        <svg viewBox="0 0 10 10" aria-hidden="true"><path d="M2 0.5 L3.6 0.5 L4 3 L2.9 3.8 Q3.8 6 6.2 7.1 L7 6 L9.5 6.4 L9.5 8 Q9.5 9.5 8 9.5 Q1 8.5 0.5 2 Q0.5 0.5 2 0.5 Z" fill="var(--sky)"/></svg>
        <span>+244 947 582 316</span>
      </div>
      <div class="contact__line">
        <svg viewBox="0 0 10 10" aria-hidden="true"><rect x="0.6" y="1.8" width="8.8" height="6.4" fill="none" stroke="var(--sky)" stroke-width="1"/><path d="M0.6 1.8 L5 5.4 L9.4 1.8" fill="none" stroke="var(--sky)" stroke-width="1"/></svg>
        <span>dorian.whitlock@tallow-p.example</span>
      </div>
    </div>
    <div class="rule"></div>
    <div class="back-brand">
      <span class="brand-dot"></span>
      <span class="brand-name">Tallow Partners</span>
    </div>
  </section>
</main>
</body>
</html>
```